Colin Vardek Business card

Hey there, I’m hoping to have a business card designed. I’m in Real estate and just switched to a new Brokerage called: The Harbourline Property Group

The back could just be the company name maybe or whatever looks good!

I’ve attached some logos of our company and some cards my buddy had done up.

On the card:
Colin Vardek
colinvardek@mailora.com
587-412-9065
colinvardek.ca

Target Market(s)

Home buyers and sellers

Industry/Entity Type

Real Estate

Contact Information for Business Card

just looking for a cool and modern design with my picture on it. I like the idea of Black and red being used.

Requirements
Must have
• all the details provided. I'm open to anything. Just want a professional looking card.

```html
<!DOCTYPE html>
<html lang="en">
<head>
<meta charset="UTF-8">
<title>Colin Vardek – Business Card</title>
<link href="https://fonts.googleapis.com/css2?family=Poppins:wght@300;400;600;700&display=swap" rel="stylesheet">
<style>
  :root {
    --stage: #232323;
    --card-dark: #222226;
    --brand-red: #d0223c;
    --line-red: #e02030;
    --foil: #f4cdb8;
    --white: #ffffff;
    --muted: #e6e6ea;
    --photo-light: #f2f2f2;
    --photo-dark: #3a3a40;
  }
  * { box-sizing: border-box; margin: 0; padding: 0; }
  html, body {
    width: 1200px; height: 711px; overflow: hidden;
    background: var(--stage);
    font-family: "Poppins", sans-serif;
  }
  .stage {
    position: relative; width: 1200px; height: 711px;
    display: flex; justify-content: center; align-items: center; gap: 60px;
  }
  .card {
    position: relative; width: 320px; height: 540px;
    overflow: hidden;
  }
  /* Back side */
  .card-back {
    background: var(--brand-red);
    border-radius: 160px 0 160px 0;
    display: flex; align-items: center; justify-content: center;
  }
  .back-name {
    color: var(--foil);
    font-weight: 600;
    font-size: 38px;
    line-height: 1.1;
    text-transform: uppercase;
    letter-spacing: 1px;
    text-align: left;
  }
  /* Front side */
  .card-front {
    background: var(--card-dark);
    border: 2px solid var(--line-red);
    border-radius: 0 160px 0 160px;
    padding: 48px 30px 0 30px;
  }
  .front-brand {
    color: var(--white);
    font-weight: 600;
    font-size: 15px;
    text-transform: uppercase;
    letter-spacing: 1px;
    line-height: 1.2;
  }
  .portrait {
    display: block;
    width: 168px; height: 168px;
    margin: 70px 0 0 60px;
    border-radius: 50%;
    border: 3px solid var(--line-red);
    background: radial-gradient(circle at 50% 40%, var(--photo-light) 45%, var(--photo-dark) 100%);
  }
  .agent-name {
    margin: 20px 0 0 20px;
    font-size: 34px;
    line-height: 1.1;
  }
  .agent-name .first { color: var(--brand-red); font-weight: 700; }
  .agent-name .last { color: var(--white); font-weight: 400; }
  .contact-list {
    list-style: none;
    margin: 16px 0 0 22px;
  }
  .contact-item {
    display: flex; align-items: center; gap: 10px;
    color: var(--muted);
    font-weight: 300;
    font-size: 14px;
    line-height: 1.9;
  }
  .contact-icon { width: 14px; height: 14px; flex: none; }
</style>
</head>
<body>
<main class="stage">
  <section class="card card-back" aria-label="Card back">
    <p class="back-name">The<br>Harbourline<br>Property<br>Group</p>
  </section>

  <section class="card card-front" aria-label="Card front">
    <p class="front-brand">The Harbourline<br>Property Group</p>
    <div class="portrait" role="img" aria-label="Portrait photo of Colin Vardek"></div>
    <h1 class="agent-name"><span class="first">Colin</span> <span class="last">Vardek</span></h1>
    <ul class="contact-list">
      <li class="contact-item">
        <svg class="contact-icon" viewBox="0 0 24 24" aria-hidden="true"><path fill="#d0223c" d="M6.6 10.8a15.1 15.1 0 006.6 6.6l2.2-2.2a1 1 0 011-.25 11.4 11.4 0 003.6.57 1 1 0 011 1V20a1 1 0 01-1 1A17 17 0 013 4a1 1 0 011-1h3.5a1 1 0 011 1 11.4 11.4 0 00.57 3.6 1 1 0 01-.25 1z"/></svg>
        587-412-9065
      </li>
      <li class="contact-item">
        <svg class="contact-icon" viewBox="0 0 24 24" aria-hidden="true"><circle cx="12" cy="12" r="9" fill="none" stroke="#d0223c" stroke-width="2"/><path d="M3 12h18M12 3c3 3 3 15 0 18M12 3c-3 3-3 15 0 18" fill="none" stroke="#d0223c" stroke-width="1.6"/></svg>
        www.colinvardek.ca
      </li>
      <li class="contact-item">
        <svg class="contact-icon" viewBox="0 0 24 24" aria-hidden="true"><rect x="3" y="6" width="18" height="13" rx="1" fill="#d0223c"/><path d="M3 7l9 7 9-7" fill="none" stroke="#222226" stroke-width="1.6"/></svg>
        colinvardek@mailora.com
      </li>
    </ul>
  </section>
</main>
</body>
</html>
```